International Travel Technology R&D business needs a wordpress website

We are a start up team of initially 2 individuals but plan to grow our team quickly, we have deep experience in travel technology. Our goal is to provide next generation technology research and development on behalf of our clients who are leading players in the travel technology industry. Attached our logos.

Target Market(s)

Travel Technology companies

Industry/Entity Type

Travel Industry

Coding

Coded - Design and coding required

Font styles to use
Sans Serif

Requirements
Must have
• Make use of our logo and colour scheme in the attached. Has to have a sense of adventure/ stepping into the unknown but equally must convey a sense of professionalism , we are a safe pair of hands. Sample themes are in the attachment .
Nice to have
• We have identified a theme on skinharbor which we feel would be inspirational. We hahe attached them to help in the design as inspiration.
Should not have
• images of airplanes , hotels etc, we want to project a future image.

```html
<!DOCTYPE html>
<html lang="en">
<head>
<meta charset="utf-8">
<title>Farway Labs</title>
<link rel="stylesheet" href="https://fonts.googleapis.com/css2?family=Maven+Pro:wght@400;500;700&family=Open+Sans:ital,wght@0,400;0,600;0,700;1,400&display=swap">
<style>
:root{
  --navy:#0b2673;
  --navy-deep:#081d5c;
  --navy-bar:#0d2c7a;
  --blue:#1f3f93;
  --green:#5b9b2f;
  --green-dark:#4c8626;
  --ink:#1b2340;
  --text:#6b6f7a;
  --grey-bg:#efefef;
  --white:#ffffff;
}
*{box-sizing:border-box;margin:0;padding:0}
html,body{width:1200px;height:3673px;overflow:hidden}
body{font-family:"Open Sans",Arial,sans-serif;color:var(--text);background:var(--white);font-size:12px;line-height:1.75}
.section-title{font-family:"Maven Pro","Open Sans",sans-serif;font-weight:500;font-size:25px;letter-spacing:1px;color:var(--ink);text-align:center;text-transform:uppercase}
.section-title span{color:var(--navy)}
.section-intro{text-align:center;width:800px;margin:0 auto;font-size:11.5px}
.read-more{display:inline-flex;align-items:center;gap:8px;font-size:12px;color:var(--navy);text-transform:uppercase;font-weight:600;text-decoration:none}
.read-more::before{content:"»";color:var(--green);font-size:14px}

/* header */
.site-header{height:122px;display:flex;align-items:center;justify-content:space-between;padding:0 110px}
.brand{display:flex;align-items:center;gap:12px;font-family:"Maven Pro",sans-serif;font-weight:700;font-size:22px;color:var(--navy);letter-spacing:1px;text-transform:uppercase}
.brand-dot{width:22px;height:22px;border-radius:50%;background:var(--green)}
.header-call{display:flex;align-items:center;gap:12px}
.call-icon{width:44px;height:44px}
.call-label{font-size:12px;color:var(--text);line-height:1.3}
.call-number{font-family:"Maven Pro",sans-serif;font-weight:700;font-size:26px;color:var(--ink);line-height:1.1}

.main-nav{height:57px;background:var(--navy-bar);display:flex;padding-left:113px}
.main-nav a{width:137px;display:flex;align-items:center;justify-content:center;color:var(--white);text-decoration:none;font-size:12px;font-weight:600;text-transform:uppercase;border-right:1px solid rgba(255,255,255,.12)}
.main-nav a.current{background:var(--green);width:98px}

/* hero */
.hero{height:502px;position:relative;background:linear-gradient(180deg,#2d6fb8 0%,#6fa1cf 28%,#c9d6e0 48%,#8a98a6 62%,#6d5a45 82%,#4a3b2d 100%)}
.hero-photo{position:absolute;inset:0}
.hero-copy{position:absolute;left:110px;top:250px;color:var(--white)}
.hero-copy h1{font-family:"Maven Pro",sans-serif;font-weight:500;font-size:32px;letter-spacing:1px;text-transform:uppercase;margin-bottom:10px}
.hero-copy p{font-size:12.5px;line-height:1.7}
.slider-dots{position:absolute;bottom:30px;left:50%;transform:translateX(-50%);display:flex;gap:8px}
.slider-dots i{width:9px;height:9px;border-radius:50%;background:rgba(255,255,255,.5)}
.slider-dots i:first-child{background:var(--white)}

/* welcome */
.welcome{height:306px;padding-top:70px;text-align:center}
.welcome .section-intro{margin-top:24px;margin-bottom:18px;font-size:11.5px;line-height:2.3}

/* services */
.services{height:568px;background:radial-gradient(ellipse at 50% 40%,#2d4fa3 0%,var(--blue) 55%,#183486 100%);color:#cdd6ee;text-align:center;padding-top:100px}
.services .section-title{color:var(--white)}
.services .section-intro{color:#cdd6ee;width:960px;margin-top:14px}
.service-list{display:flex;justify-content:center;gap:70px;margin-top:48px}
.service{width:270px}
.service-icon{width:98px;height:98px;border-radius:50%;background:var(--green);margin:0 auto 24px;display:flex;align-items:center;justify-content:center}
.service h3{font-family:"Maven Pro",sans-serif;font-weight:500;font-size:14px;color:var(--white);text-transform:uppercase;margin-bottom:10px}
.service p{font-size:11.5px}

/* projects */
.projects{height:632px;padding-top:70px;position:relative;text-align:center}
.projects .section-intro{margin-top:14px;line-height:2.3}
.project-grid{position:absolute;left:110px;top:206px;width:977px;display:grid;grid-template-columns:repeat(4,220px);column-gap:32px;row-gap:34px}
.project{height:146px}
.project-feature{background:var(--green);color:var(--white);text-align:center;padding:32px 18px 0}
.project-feature h4{font-family:"Maven Pro",sans-serif;font-size:13px;font-weight:700;text-transform:uppercase;margin-bottom:8px}
.project-feature p{font-size:11px;line-height:1.6}
.slide-arrow{position:absolute;top:370px;width:20px;height:30px}
.slide-arrow.prev{left:62px}
.slide-arrow.next{right:62px}

/* reviews */
.reviews{height:475px;background:var(--grey-bg);padding-top:82px;text-align:center;position:relative}
.review-quote{width:960px;margin:26px auto 0;font-style:italic;font-size:11.5px;line-height:2.2;color:#8a8d95;position:relative}
.quote-mark{position:absolute;font-family:Georgia,serif;font-size:48px;color:#8a8d95;line-height:1}
.quote-mark.open{left:-6px;top:-30px}
.quote-mark.close{right:-6px;bottom:-34px}
.reviewer{display:flex;align-items:center;justify-content:center;gap:30px;margin-top:50px}
.reviewer-photo{width:78px;height:78px;border-radius:50%;background:linear-gradient(160deg,#c9b59a,#7a6350);border:3px solid var(--white);box-shadow:0 0 0 1px #ccc}
.reviewer-name{font-family:"Maven Pro",sans-serif;font-size:13px;color:var(--green);text-transform:uppercase;font-weight:500;margin-top:14px}
.stars{color:#f2a51a;font-size:13px;letter-spacing:1px}

/* news */
.news{height:603px;padding-top:80px}
.news-list{display:flex;gap:30px;margin:40px 0 0 110px}
.news-card{width:306px}
.news-image{height:204px}
.news-head{display:flex;align-items:center;gap:16px;height:64px}
.news-date{width:64px;height:64px;flex:none;background:var(--green);color:var(--white);text-align:center;font-family:"Maven Pro",sans-serif;padding-top:6px}
.news-date small{display:block;font-size:12px;line-height:1.2}
.news-date b{display:block;font-size:28px;line-height:1.1;font-weight:500}
.news-title{font-size:12px;font-weight:700;color:var(--ink);line-height:1.8}
.news-card p{font-size:11px;margin:12px 0 14px;line-height:1.95}

/* footer */
.site-footer{height:310px;background:var(--navy);color:#c3cbe4;display:flex;padding:52px 0 0 110px}
.footer-col h5{font-family:"Maven Pro",sans-serif;font-weight:500;font-size:15px;color:var(--white);text-transform:uppercase;margin-bottom:14px;letter-spacing:.5px}
.footer-about{width:407px}
.footer-about p{width:300px;font-size:11px;line-height:1.9}
.footer-contact{display:flex;align-items:center;gap:14px;color:var(--white);font-size:13px;font-weight:600;margin-top:18px}
.footer-contact .dot{width:38px;height:38px;border-radius:50%;background:var(--green);display:flex;align-items:center;justify-content:center}
.footer-links{width:250px}
.footer-links ul{list-style:none}
.footer-links li{font-size:11px;color:var(--white);line-height:2.45}
.footer-news p{width:310px;font-size:11px;line-height:1.9}
.subscribe{display:flex;margin-top:36px;width:305px;height:46px;background:var(--white)}
.subscribe span{flex:1;padding:0 12px;display:flex;align-items:center;font-size:11px;color:#9a9da6}
.subscribe i{width:40px;margin:6px;background:var(--green);display:flex;align-items:center;justify-content:center}

.bottom-bar{height:98px;background:var(--navy-deep);display:flex;align-items:center;justify-content:space-between;padding:0 110px;color:#c3cbe4;font-size:11px}
.social{display:flex;align-items:center;gap:8px}
.social i{width:22px;height:22px;border-radius:50%;background:#3d7fd1}
</style>
</head>
<body>

<header class="site-header">
  <div class="brand"><span class="brand-dot"></span>Farway Labs</div>
  <div class="header-call">
    <svg class="call-icon" viewBox="0 0 44 44" aria-hidden="true"><circle cx="22" cy="22" r="20" fill="none" stroke="#5b9b2f" stroke-width="3"/><path d="M15 12c1-1 3-1 4 1l2 4c.5 1 0 2-1 3l-1 1c1 3 4 6 7 7l1-1c1-1 2-1.5 3-1l4 2c2 1 2 3 1 4l-2 2c-3 2-9-1-14-6s-8-11-6-14z" fill="#5b9b2f"/></svg>
    <div>
      <div class="call-label">For Information Call Us Now!</div>
      <div class="call-number">(555) 010-4567</div>
    </div>
  </div>
</header>

<nav class="main-nav">
  <a class="current">Home</a><a>About</a><a>Our Services</a><a>Projects</a><a>Latest News</a><a>Contact Us</a><a>Career</a>
</nav>

<section class="hero">
  <div class="hero-photo" role="img" aria-label="Photo of a traveller in a yellow jacket working on a laptop beside an orange tent in snowy mountains at sunrise"></div>
  <div class="hero-copy">
    <h1>Travel Technology Industry</h1>
    <p>Lorem ipsum dolor sit amet, consectetur adipiscing elit. Nunc varius posuere quam ac auctor.<br>Phasellus ultricies suscipit dui quis sagittis. Phasellus vulputate vulputate urna.</p>
  </div>
  <div class="slider-dots"><i></i><i></i><i></i></div>
</section>

<section class="welcome">
  <h2 class="section-title">Welcome to <span>Farway Labs</span></h2>
  <p class="section-intro">Lorem ipsum dolor sit amet, consectetur adipiscing elit. Aliquam in feugiat magna. Proin eu semper sem, vel efficitur dolor. Donec non posuere mi. Donec vulputate consequat massa et sodales. Vestibulum ante ipsum primis in faucibus orci luctus et ultrices posuere cubilia Curae; Cras nec semper velit, non iaculis neque. Integer vehicula bibendum scelerisque.</p>
  <a class="read-more">Read More</a>
</section>

<section class="services">
  <h2 class="section-title">Our Services</h2>
  <p class="section-intro">Vestibulum ante ipsum primis in faucibus orci luctus et ultrices posuere cubilia Curae; Cras nec semper velit, non iaculis neque. Integer vehicula bibendum scelerisque. Donec a ligula dolor. Phasellus gravida vehicula ipsum, ultr ices lacinia dui pellentesque at. Etiam pharetra ante orci, eget pretium nulla suscipit non.</p>
  <div class="service-list">
    <div class="service">
      <div class="service-icon"><svg width="34" height="34" viewBox="0 0 34 34" aria-hidden="true"><circle cx="14" cy="14" r="9" fill="none" stroke="#fff" stroke-width="4"/><path d="M21 21l8 8" stroke="#fff" stroke-width="5" stroke-linecap="round"/></svg></div>
      <h3>Technology Research</h3>
      <p>Donec rutrum tincidunt libero, quis sodales urna vulputate in. Etiam nec mollis magna, vel commodo est. Aliquam enim ligula, dapibus id ipsum.</p>
    </div>
    <div class="service">
      <div class="service-icon"><svg width="38" height="34" viewBox="0 0 38 34" aria-hidden="true"><rect x="2" y="2" width="34" height="22" rx="2" fill="none" stroke="#fff" stroke-width="3.5"/><path d="M14 31h10M19 24v7" stroke="#fff" stroke-width="3.5"/></svg></div>
      <h3>Technology Development</h3>
      <p>Donec rutrum tincidunt libero, quis sodales urna vulputate in. Etiam nec mollis magna, vel commodo est. Aliquam enim ligula, dapibus id ipsum.</p>
    </div>
    <div class="service">
      <div class="service-icon"><svg width="36" height="36" viewBox="0 0 36 36" aria-hidden="true"><path d="M33 3c-2-1-5 0-7 2l-5 5L6 7 3 10l12 6-5 5-5-1-2 2 6 3 3 6 2-2-1-5 5-5 6 12 3-3-3-15 5-5c2-2 3-5 2-7z" fill="#fff"/></svg></div>
      <h3>Travel Technology</h3>
      <p>Donec rutrum tincidunt libero, quis sodales urna vulputate in. Etiam nec mollis magna, vel commodo est. Aliquam enim ligula, dapibus id ipsum.</p>
    </div>
  </div>
</section>

<section class="projects">
  <h2 class="section-title">Recent <span>Projects</span></h2>
  <p class="section-intro">Donec non posuere mi. Donec vulputate consequat massa et sodales. Vestibulum ante ipsum primis in faucibus orci luctus et ultrices posuere cubilia Curae; Cras nec semper velit, non iaculis neque. Integer vehicula bibendum scelerisque.</p>
  <svg class="slide-arrow prev" viewBox="0 0 20 30" aria-hidden="true"><path d="M15 4L5 15l10 11" fill="none" stroke="#999" stroke-width="3"/></svg>
  <svg class="slide-arrow next" viewBox="0 0 20 30" aria-hidden="true"><path d="M5 4l10 11L5 26" fill="none" stroke="#999" stroke-width="3"/></svg>
  <div class="project-grid">
    <div class="project" role="img" aria-label="Businessman touching glowing digital icons" style="background:linear-gradient(135deg,#0f1e3a,#1d4e8a 60%,#0c1628)"></div>
    <div class="project" role="img" aria-label="Travel planning desk with notebook and compass" style="background:linear-gradient(135deg,#d9e4e8,#b4c7cc 60%,#e9eef0)"></div>
    <div class="project project-feature">
      <h4>Lorem ipsum dolor sit</h4>
      <p>Maecenas quis tristique sapien, id amet sodales mauris. Maecenas elementum arcu est.</p>
    </div>
    <div class="project" role="img" aria-label="Hands holding a smartphone outdoors" style="background:linear-gradient(135deg,#8b6b4e,#b08c6a 55%,#6e5641)"></div>
    <div class="project" role="img" aria-label="Globe with connected travel icons" style="background:linear-gradient(135deg,#e7eef8,#8fb4e2 55%,#cfe0f4)"></div>
    <div class="project" role="img" aria-label="Woman with a laptop sitting by a bright window" style="background:linear-gradient(135deg,#d8d2c4,#a8b08f 55%,#e6e1d6)"></div>
    <div class="project" role="img" aria-label="Hand holding a glowing digital globe" style="background:linear-gradient(135deg,#2a2530,#7d4f8e 55%,#1c1a22)"></div>
    <div class="project" role="img" aria-label="Traveller with luggage in a glass terminal" style="background:linear-gradient(135deg,#dfe2e4,#a5abb0 55%,#eceeef)"></div>
  </div>
</section>

<section class="reviews">
  <h2 class="section-title">Customer <span>Reviews</span></h2>
  <p class="review-quote">
    <span class="quote-mark open">“</span>
    Cras aliquam in nunc vel tempor. Aliquam tortor nunc, pretium quis imperdiet sit amet, sodales sed lectus. Vivamus id ante a augue fringilla vulputate eu sed mi. Nunc ornare neque non risus gravida, eget commodo nulla lobortis. Suspendisse tempus tortor eget erat venenatis hendrerit. Morbi rutrum sem ultrices nibh varius, sed placerat lorem consectetur. Nullam egestas nisi ornare sapien scelerisque, nec ornare nisi vulputate. Cras iaculis finibus lacus sed sagittis.
    <span class="quote-mark close">”</span>
  </p>
  <div class="reviewer">
    <svg width="14" height="22" viewBox="0 0 14 22" aria-hidden="true"><path d="M11 3L3 11l8 8" fill="none" stroke="#777" stroke-width="2.5"/></svg>
    <div class="reviewer-photo" role="img" aria-label="Customer portrait"></div>
    <svg width="14" height="22" viewBox="0 0 14 22" aria-hidden="true"><path d="M3 3l8 8-8 8" fill="none" stroke="#777" stroke-width="2.5"/></svg>
  </div>
  <div class="reviewer-name">Marek Lund</div>
  <div class="stars">★★★★★</div>
</section>

<section class="news">
  <h2 class="section-title">Latest News &amp; Updates</h2>
  <div class="news-list">
    <article class="news-card">
      <div class="news-image" role="img" aria-label="Team gathered around a large glowing globe" style="background:linear-gradient(160deg,#6f9fd0,#2f5f98 45%,#b89a82)"></div>
      <div class="news-head">
        <div class="news-date"><small>AUG</small><b>14</b></div>
        <h4 class="news-title">Lorem ipsum dolor sit amet, conse ctetur adipiscing elit.</h4>
      </div>
      <p>Proin eu semper sem, vel efficitur dolor. Donec non posuere mi. Donec vulputate consequat massa et sodales. Vestibulum ante ipsum primis in faucibus.</p>
      <a class="read-more">Read More</a>
    </article>
    <article class="news-card">
      <div class="news-image" role="img" aria-label="Laptop on a wooden table in a golden field" style="background:linear-gradient(180deg,#f1d48a,#d69a3c 45%,#8a5a2b)"></div>
      <div class="news-head">
        <div class="news-date"><small>AUG</small><b>13</b></div>
        <h4 class="news-title">Lorem ipsum dolor sit amet, conse ctetur adipiscing elit.</h4>
      </div>
      <p>Proin eu semper sem, vel efficitur dolor. Donec non posuere mi. Donec vulputate consequat massa et sodales. Vestibulum ante ipsum primis in faucibus.</p>
      <a class="read-more">Read More</a>
    </article>
    <article class="news-card">
      <div class="news-image" role="img" aria-label="Man with a phone sitting beside a bicycle in a city" style="background:linear-gradient(160deg,#b9bcb8,#6e706b 50%,#3f403c)"></div>
      <div class="news-head">
        <div class="news-date"><small>AUG</small><b>12</b></div>
        <h4 class="news-title">Lorem ipsum dolor sit amet, conse ctetur adipiscing elit.</h4>
      </div>
      <p>Proin eu semper sem, vel efficitur dolor. Donec non posuere mi. Donec vulputate consequat massa et sodales. Vestibulum ante ipsum primis in faucibus.</p>
      <a class="read-more">Read More</a>
    </article>
  </div>
</section>

<footer class="site-footer">
  <div class="footer-col footer-about">
    <h5>Farway Labs</h5>
    <p>Nunc eget dui quam. Sed vitae tincidunt felis, quis mattis eros. Integer facilisis augue enim, eu lacinia mi malesua da vitae. Praesent fringilla sodales tortor.</p>
    <div class="footer-contact"><span class="dot"><svg width="16" height="16" viewBox="0 0 16 16" aria-hidden="true"><path d="M3 1c1-1 2 0 2.5 1l1 2c.3.7 0 1.3-.6 1.8l-.6.5c.7 1.8 2.2 3.3 4 4l.5-.6c.5-.6 1.1-.9 1.8-.6l2 1c1 .5 2 1.5 1 2.5l-1 1C12 15 8 13 5.5 10.5S1 4 2 2.5z" fill="#fff"/></svg></span>(555) 010-4567</div>
    <div class="footer-contact"><span class="dot"><svg width="16" height="12" viewBox="0 0 16 12" aria-hidden="true"><rect x="0.5" y="0.5" width="15" height="11" fill="none" stroke="#fff"/><path d="M1 1l7 6 7-6" fill="none" stroke="#fff"/></svg></span>info@farwaylabs.example</div>
  </div>
  <div class="footer-col footer-links">
    <h5>Quick Links</h5>
    <ul><li>Home</li><li>About us</li><li>Services</li><li>Projects</li><li>Contact us</li><li>Privacy Policy</li></ul>
  </div>
  <div class="footer-col footer-news">
    <h5>Signup Our Newsletter</h5>
    <p>Lorem ipsum dolor sit amet, consectetur adipiscing elit. Aliquam in feugiat magna. Proin eu semper sem, vel efficitur dolor. Donec non posuere mi.</p>
    <div class="subscribe"><span>Email Address</span><i><svg width="14" height="14" viewBox="0 0 14 14" aria-hidden="true"><path d="M1 7h11M7 2l5 5-5 5" fill="none" stroke="#fff" stroke-width="2"/></svg></i></div>
  </div>
</footer>

<div class="bottom-bar">
  <span>Copyrights © 2016 Farway. All Right Reserved.</span>
  <div class="social">Connect Us : <i></i><i></i><i></i><i></i></div>
</div>

</body>
</html>
```